Medical centre needs a business card

We are a medcial centre in Australia, needing a new business card. Our demographic is low working class families. We are going to be renovating our premises to modernise the look and also had a new logo done a few months ago representing quality and community, and now need to update our cards. It needs to be doubled sided, with logo and contact details on the front, and appointment details on the back. . Needs to be modern and simple, easy to read. <br/><br/>Name: Kindle Grove Medical Centre <br/>Address: 512 Parmley Rd (Cnr Parmley Rd & Osgood Creek Rd),<br/>Tindarra Court Shopping Centre, Ashbridge, SA 5999<br/>Ph: 08 8461 3072<br/>Tag line: Where your wellbeing comes first<br/>Website: www.kindlegrovemedicalcentre-example.com.au<br/>Online bookings also available<br/><br/>(On the back, to have 3 lines of appointments that can be written in.<br/>Day, date, time)<br/><br/>Your next appointment is on<br/>Can try “M T W Th F Sa Su _________________ at ____________ am/pm” or other combinations <br/>Please advise as soon as possible if unable to attend<br/>Cancellation fees apply if less than 2 hrs notice<br/>Online appointments available (please highlight this option by either by position, colour or font)

Target Market(s)

Lower social economic working class, young families to seniors

Industry/Entity Type

Medical Centre

Contact Information for Business Card

Kindle Grove Medical Centre
512 Parmley Rd (Cnr Parmley Rd & Osgood Creek Drive)
Tindarra Court Shopping Centre
Paralowie SA 5108
Ph: 08 8461 3072
www.kindlegrovemedicalcentre-example.com.au
Tagline line: where your wellbeing comes first
Back side is for appointments
Your next appointment is with Dr ______________
Day/date/time (Please give 3 lines of appointments)
Please advise as soon as possible if unable to attend
Cancellation fees apply if less than 2 hours notice
Online appointments available
Book online easily and conveniently (please highlight online appointments)

Font styles to use
Serif
Sans Serif

Colors

Designer to choose colors to be used in the design.

Requirements
Must have
• Modern and simple
• Easy to ready
• Induces a wellbeing feeling
• Incorporate our logo colours and feel from logo
• Induces feeling of stability and security
Nice to have
• Attract attention
• Pleasant to look at
• Feeling of innovation
Should not have
• Loud clashing colours
• Overly luxurious feeling
• Overly artistic

```html
<!DOCTYPE html>
<html lang="en">
<head>
<meta charset="utf-8">
<title>Kindle Grove Medical Centre – Business Card</title>
<link href="https://fonts.googleapis.com/css2?family=Josefin+Sans:wght@400;600;700&display=swap" rel="stylesheet">
<style>
  :root {
    --bg: #2b2b2d;
    --card-white: #ffffff;
    --card-dark: #1d1d1f;
    --blue: #1670c0;
    --blue-band: #166fbf;
    --green: #9bcb3b;
    --text-light: #f2f2f2;
  }
  * { box-sizing: border-box; margin: 0; padding: 0; }
  html, body { width: 1200px; height: 900px; overflow: hidden; }
  body {
    background: var(--bg);
    font-family: "Josefin Sans", Arial, sans-serif;
    position: relative;
  }
  .card {
    position: absolute;
    left: 240px;
    width: 720px;
    height: 410px;
    border-radius: 18px;
    overflow: hidden;
  }

  /* ---------- Appointment side ---------- */
  .card-back { top: 25px; background: var(--card-white); color: var(--blue); }
  .appt-title {
    position: absolute; left: 56px; top: 34px; width: 608px; height: 52px;
    border: 2px solid var(--green);
    display: flex; align-items: center; justify-content: center;
    font-weight: 700; font-size: 24px; letter-spacing: 2px;
  }
  .field { position: absolute; left: 40px; font-weight: 600; font-size: 19px; display: flex; align-items: flex-end; }
  .line { display: inline-block; border-bottom: 1.5px solid var(--green); height: 18px; }
  .field-name { top: 106px; }
  .field-date { top: 150px; }
  .slash { padding: 0 4px; }
  .field-time { position: absolute; left: 395px; top: 150px; font-weight: 600; font-size: 19px; display: flex; align-items: flex-end; }
  .ampm { margin-left: 8px; font-weight: 700; font-size: 20px; }
  .days {
    position: absolute; left: 40px; top: 198px; width: 640px;
    display: flex; justify-content: space-between;
    font-weight: 600; font-size: 15px;
  }
  .day { display: flex; align-items: center; gap: 6px; }
  .box { width: 12px; height: 12px; border: 1.5px solid var(--green); display: inline-block; }
  .notice {
    position: absolute; left: 40px; top: 238px; width: 640px;
    font-size: 18px; line-height: 26px; letter-spacing: 1.2px;
  }
  .notice-first { border-bottom: 1.5px solid var(--green); padding-bottom: 2px; }
  .online-band {
    position: absolute; left: 0; bottom: 0; width: 100%; height: 92px;
    background: var(--blue-band); color: #fff;
    display: flex; align-items: center; justify-content: center;
    font-weight: 700; font-size: 21px; letter-spacing: 7px;
    padding-top: 8px;
  }

  /* ---------- Contact side ---------- */
  .card-front { top: 465px; background: var(--card-dark); color: var(--text-light); }
  .accent-bar { position: absolute; left: 28px; top: 40px; width: 9px; height: 54px; background: var(--green); }
  .person-name { position: absolute; left: 52px; top: 40px; font-size: 38px; font-weight: 600; color: var(--green); letter-spacing: 1px; }
  .person-role { position: absolute; left: 52px; top: 84px; font-size: 22px; letter-spacing: 1px; }
  .brand {
    position: absolute; right: 34px; top: 46px;
    display: flex; align-items: center; gap: 12px;
    font-size: 19px; font-weight: 700; color: var(--blue); text-transform: uppercase; letter-spacing: 1px;
    text-align: right; line-height: 24px;
  }
  .brand-square { width: 44px; height: 44px; background: var(--blue); flex: none; }
  .address { position: absolute; left: 52px; top: 158px; font-size: 21px; line-height: 30px; letter-spacing: 1px; }
  .contact { position: absolute; left: 44px; top: 232px; font-size: 21px; line-height: 32px; letter-spacing: 1px; }
  .contact .label { color: var(--blue); margin-right: 8px; }
  .contact .web-main { color: var(--blue); }
  .tagline {
    position: absolute; left: 0; width: 100%; top: 330px; text-align: center;
    font-size: 27px; color: var(--green); letter-spacing: 1px;
  }
</style>
</head>
<body>

<section class="card card-back" aria-label="Appointment side">
  <div class="appt-title">YOUR NEXT APPOINTMENT</div>
  <div class="field field-name">Name :&nbsp;<span class="line" style="width:560px"></span></div>
  <div class="field field-date">Date :&nbsp;<span class="line" style="width:60px"></span><span class="slash">/</span><span class="line" style="width:60px"></span><span class="slash">/</span><span class="line" style="width:95px"></span></div>
  <div class="field-time">Time :&nbsp;<span class="line" style="width:150px"></span><span class="ampm">AM/PM</span></div>
  <div class="days">
    <span class="day"><span class="box"></span>MON</span>
    <span class="day"><span class="box"></span>TUE</span>
    <span class="day"><span class="box"></span>WED</span>
    <span class="day"><span class="box"></span>THU</span>
    <span class="day"><span class="box"></span>FRI</span>
    <span class="day"><span class="box"></span>SAT</span>
    <span class="day"><span class="box"></span>SUN</span>
  </div>
  <p class="notice"><span class="notice-first">Please advise as soon as possible if unable to attend</span><br>Cancellation fees apply if less than 2 hours notice.</p>
  <div class="online-band">ONLINE APPOINTMENTS AVAILABLE</div>
</section>

<section class="card card-front" aria-label="Contact side">
  <div class="accent-bar"></div>
  <div class="person-name">MARTIN CLARKE</div>
  <div class="person-role">Manager</div>
  <div class="brand"><span>Kindle Grove<br>Medical Centre</span><span class="brand-square"></span></div>
  <p class="address">512 Parmley Rd Tindarra Court Shopping Centre,<br>Ashbridge, SA 5999</p>
  <p class="contact">
    <span class="label">P:</span>08 8461 3072<br>
    <span class="label">W:</span>www.<span class="web-main">kindlegrovemedicalcentre-example</span>.com.au
  </p>
  <p class="tagline">Where your wellbeing comes first</p>
</section>

</body>
</html>
```